New Business Card Design for Manufacturing

We are an engineering/manufacturing company that offers Advanced machining/assembly/engineering services, as well as innovative products for the heavy duty engine cooling markets.

We are looking to get a new business card designed that is clean and modern looking, but still fits the wide range of technical/skilled work we do.

- We hope to use this design as the base for other design work in new Presentations, web, and print work.

Industry/Entity Type

Engineering

Contact Information for Business Card

Our preferred color of blue is (RGB) 22/71/159 but can vary slightly from that color. Our content will be our Logo and full company name (Vantrell Forge Works, Inc.), company address, name, job title, phone number with extension, cell number, fax number, website, and email address on the cards.
We'd like the full company name next to the logo, but we are open to other interpretations of that layout.
Preferably, we would like the back side to be clean with just our logo, and the front to contain all of the contact information.

Colors
2f74b4
0355a3
85abd2

Requirements
Must have
• - Logo, company name, needed content - We are open to interpretation beyond that.
• - Standard size business card.
• - Horizontal orientation.
• - Enough space for lengthy names / job titles (for example, a job title could read "Directory of Human Resources" or "V.P. of Governmental Affairs"). We need this to look clean, whether the title be short (CEO) or long (as described above).

```html
<!DOCTYPE html>
<html lang="en">
<head>
<meta charset="utf-8">
<title>Vantrell Forge Works – Business Card</title>
<link href="https://fonts.googleapis.com/css2?family=Fira+Sans:wght@500;600&family=Open+Sans:wght@400;600&display=swap" rel="stylesheet">
<style>
  :root {
    --page-bg: #e6e8eb;
    --card-bg: #f7f8fa;
    --brand-blue: #16479f;
    --wave-blue: #1f5d9c;
    --wave-blue-deep: #16478a;
    --steel-grey: #8d939b;
    --steel-light: #c9ccd1;
    --text-dark: #3a3d42;
    --text-light: #f2f4f7;
    --address-grey: #c7ccd3;
  }
  * { box-sizing: border-box; margin: 0; padding: 0; }
  html, body { width: 1200px; height: 1047px; overflow: hidden; }
  body { background: var(--page-bg); position: relative; font-family: "Open Sans", sans-serif; }

  .card {
    position: absolute; left: 100px; top: 225px;
    width: 1000px; height: 596px;
    background: var(--card-bg);
    overflow: hidden;
    box-shadow: 0 10px 30px rgba(0,0,0,.18);
  }
  .card-waves { position: absolute; inset: 0; width: 1000px; height: 596px; }

  .holder-marker {
    position: absolute; left: -22px; top: 80px;
    width: 40px; height: 52px; border-radius: 50%;
    background: var(--brand-blue);
  }
  .holder-name {
    position: absolute; left: 47px; top: 62px;
    font-family: "Fira Sans", sans-serif; font-weight: 500;
    font-size: 37px; color: var(--brand-blue);
  }
  .holder-title {
    position: absolute; left: 47px; top: 112px;
    font-size: 22px; color: var(--text-dark);
  }

  .brand-mark {
    position: absolute; left: 515px; top: 78px; width: 430px;
    text-align: center;
  }
  .brand-name {
    font-family: "Fira Sans", sans-serif; font-weight: 600;
    font-size: 76px; letter-spacing: 4px; color: var(--brand-blue); line-height: 1;
  }
  .brand-tagline {
    margin-top: 14px;
    font-family: "Fira Sans", sans-serif; font-weight: 600;
    font-size: 22px; letter-spacing: 1px; color: var(--steel-grey);
  }
  .company-name {
    position: absolute; right: 44px; top: 260px;
    font-family: "Fira Sans", sans-serif; font-weight: 500;
    font-size: 28px; color: var(--brand-blue);
  }

  .contact-list { position: absolute; left: 50px; top: 386px; list-style: none; }
  .contact-item {
    display: flex; align-items: center; height: 35.5px;
    font-size: 24px; color: var(--text-light);
  }
  .contact-icon { width: 22px; height: 22px; margin-right: 15px; fill: var(--text-light); }

  .address {
    position: absolute; right: 44px; top: 492px;
    font-size: 24px; line-height: 35px; text-align: right; color: var(--address-grey);
  }
</style>
</head>
<body>
  <div class="card">
    <svg class="card-waves" viewBox="0 0 1000 596" aria-hidden="true">
      <path fill="var(--wave-blue)" d="M0,300 C220,285 440,330 640,405 C780,455 900,420 1000,368 L1000,596 L0,596 Z"/>
      <path fill="var(--steel-light)" d="M0,252 C250,232 470,285 650,350 C800,404 910,378 1000,322 L1000,362 C900,418 790,440 640,390 C470,330 250,288 0,300 Z"/>
      <path fill="var(--steel-grey)" d="M0,250 C260,228 480,282 660,345 C790,390 900,372 1000,318 L1000,330 C900,388 790,408 655,362 C480,300 260,250 0,268 Z"/>
      <path fill="var(--steel-grey)" d="M470,375 C620,405 780,400 1000,352 L1000,362 C800,420 640,422 470,375 Z"/>
      <path fill="var(--steel-grey)" d="M500,395 C650,430 810,418 1000,372 L1000,380 C820,432 660,440 500,395 Z"/>
    </svg>

    <div class="holder-marker"></div>
    <h1 class="holder-name">Marlon Reyes Ashby</h1>
    <p class="holder-title">Managing Director</p>

    <div class="brand-mark">
      <div class="brand-name">VANTRELL</div>
      <div class="brand-tagline">BUILT FOR WHAT'S NEXT</div>
    </div>
    <p class="company-name">Vantrell Forge Works, Inc.</p>

    <ul class="contact-list">
      <li class="contact-item">
        <svg class="contact-icon" viewBox="0 0 24 24"><path d="M3 9c0-3 4-5 9-5s9 2 9 5l-4 1-1-2H8L7 10zM6 12h12l2 8H4z"/></svg>
        555-0142-7100 (VFW)
      </li>
      <li class="contact-item">
        <svg class="contact-icon" viewBox="0 0 24 24"><path d="M7 2h10a1 1 0 0 1 1 1v18a1 1 0 0 1-1 1H7a1 1 0 0 1-1-1V3a1 1 0 0 1 1-1zm1 3v12h8V5z"/></svg>
        555-0187-2263
      </li>
      <li class="contact-item">
        <svg class="contact-icon" viewBox="0 0 24 24"><path d="M7 3h10v5H7zM4 9h16v8h-3v4H7v-4H4zm5 6v4h6v-4z"/></svg>
        555-0119-4408
      </li>
      <li class="contact-item">
        <svg class="contact-icon" viewBox="0 0 24 24"><path d="M2 5h20v14H2zm2 2v1l8 5 8-5V7l-8 5z"/></svg>
        mashby@vantrellforge.com
      </li>
      <li class="contact-item">
        <svg class="contact-icon" viewBox="0 0 24 24"><path d="M12 2a10 10 0 1 0 0 20 10 10 0 0 0 0-20zm-1 2.1V11H5a7 7 0 0 1 6-6.9zM13 4.1A7 7 0 0 1 19 11h-6zM5 13h6v6.9A7 7 0 0 1 5 13zm8 0h6a7 7 0 0 1-6 6.9z"/></svg>
        www.vantrellforge.com
      </li>
    </ul>

    <address class="address" style="font-style:normal">
      780 Kettle Ridge Rd., Halbrook,<br>
      Ardell, US 604218
    </address>
  </div>
</body>
</html>
```